Elevate our existing website to be more luxury and add your pizazz!

We are seeking someone to bring some freshness to our recently redesigned website. I feel like it is missing some of the luxury, high end and rustic feelings we wanted from it. It is missing some pizazz! My goal was to have an intuitive, immersive, and captivating high-end website that resonates with my handmade art. I wanted a blend of creativity, rustic charm, luxury and high-end functionality, ensuring an easy-to-use and secure browsing experience that speaks to our brand of hand made and crafted items.
Design Aesthetics:
I love immersive nature. I'd love to feel like my website was a walk in the forest, the flowers, etc. Leaving the visitor feeling refreshed and inspired.
The design should seamlessly merge rustic elements with modern inspiration, evoking a sense of being surrounded by nature.
We're drawn to a moody ambiance that captures the essence of a forest, without veering into darkness.
While avoiding the typical all-white background, we aim for a balanced and visually appealing color scheme with perhaps elements floating into the frame with artful taste.
The site was designed in Elementor and I can provide you with the Wordpress login to make the changes once approved.
Branding Guide: https://www.plinthbox.com/design/QRmZtPeLqWs/VnTy82KdRoEuJxCbMa4wGp/watch?utm_content=QRmZtPeLqWs&utm_campaign=designshare&utm_medium=link&utm_source=publishsharelink
Recently redesigned website: dev.mossrivertwine.com
Target Market(s)
Luxury Crafters , Knitters and Crocheters
Industry/Entity Type
Art
Number of Pages Required
1 page

```html
<!DOCTYPE html>
<html lang="en">
<head>
<meta charset="utf-8">
<title>Moss River Twine — Made By Hand</title>
<link href="https://fonts.googleapis.com/css2?family=Allura&family=Poppins:wght@400;500;600&display=swap" rel="stylesheet">
<style>
:root{
  --ink:#111;
  --forest:#2f3d30;
  --forest-deep:#26322a;
  --moss:#3d5440;
  --mist:#e8ebe9;
  --paper:#fff;
  --line:#cfcfcf;
  --muted:#555;
}
*{margin:0;padding:0;box-sizing:border-box}
html,body{width:1200px;height:3959px;overflow:hidden}
body{position:relative;background:var(--paper);font-family:"Poppins",sans-serif;color:var(--ink)}
.abs{position:absolute}
.script{font-family:"Allura",cursive;font-weight:400}
a{color:inherit;text-decoration:none}

/* header */
.topbar{left:492px;top:0;width:542px;height:55px;background:var(--forest-deep);color:#fff;font-size:15px;display:flex;align-items:center;clip-path:polygon(0 0,100% 0,100% 100%,4% 100%)}
.topbar span{display:flex;align-items:center;gap:10px}
.topbar .phone{margin-left:55px}
.topbar .mail{margin-left:70px}
.cart{left:1063px;top:14px}
.brand{left:112px;top:52px;font-size:24px;font-weight:500;letter-spacing:.5px;display:flex;align-items:center;gap:12px}
.brand i{display:block;width:34px;height:34px;border-radius:50%;background:var(--forest)}
.brand small{position:absolute;left:46px;top:32px;font-size:11px;font-weight:400;color:var(--muted)}
.nav{top:92px;font-size:15px;font-weight:500}
.nav.active{color:var(--moss);border-bottom:2px solid var(--moss);padding-bottom:4px}

/* hero */
.hero-forest{left:0;top:360px;width:1200px;height:410px;background:linear-gradient(#fff 0%,#dfe4e0 35%,#6c7f6c 70%,var(--moss) 100%)}
.hero-title{left:112px;top:205px;font-size:60px}
.hero-tag{left:112px;top:289px;width:349px;height:46px;background:var(--ink);color:#fff;font-size:25px;font-weight:500;display:flex;align-items:center;justify-content:center;letter-spacing:.5px}
.hero-copy{left:112px;top:355px;width:520px;font-size:15.5px;line-height:37px;white-space:nowrap}
.btn{display:flex;align-items:center;justify-content:center;background:var(--ink);color:#fff;border-radius:30px;font-weight:500;letter-spacing:.5px}
.btn-shop{left:112px;top:452px;width:149px;height:45px;font-size:18px}
.hero-card{left:664px;top:166px;width:424px;height:452px;background:#fff;box-shadow:0 4px 18px rgba(0,0,0,.15)}
.hero-card div{position:absolute;inset:40px 50px;background:radial-gradient(circle at 50% 55%,#7a4d6a 0%,#b7883f 35%,#e9e4d8 65%,#fff 90%)}

/* intro */
.craft-title{left:0;top:815px;width:1200px;text-align:center;font-size:60px}
.photo-a{left:112px;top:957px;width:415px;height:336px;background:linear-gradient(135deg,#d8a43a,#eef0f2 50%,#3b2a1f)}
.photo-b{left:286px;top:1085px;width:313px;height:257px;background:#fff;box-shadow:0 4px 14px rgba(0,0,0,.18);padding:7px}
.photo-b div{width:100%;height:100%;background:linear-gradient(#5b8e9a,#d8c9a8 55%,#c9a066)}
.intro-lead{left:651px;top:963px;font-size:17px;line-height:40px;letter-spacing:.8px;text-transform:uppercase;white-space:nowrap}
.intro-copy{left:651px;top:1094px;font-size:15px;line-height:37px;white-space:nowrap}
.btn-read{left:651px;top:1268px;width:150px;height:48px;font-size:18px}
.doily{left:968px;top:1352px;width:200px;height:185px;border-radius:50%;background:radial-gradient(#f3f3f3,#e4e4e4 60%,rgba(255,255,255,0) 72%)}

/* categories */
.cats{left:128px;top:1437px;width:945px;height:271px;background:#fff;box-shadow:0 2px 12px rgba(0,0,0,.18);display:flex}
.cat{flex:1;display:flex;flex-direction:column;align-items:center;padding-top:44px;position:relative}
.cat+.cat::before{content:"";position:absolute;left:0;top:16px;bottom:16px;width:2px;background:#444}
.cat-icon{width:129px;height:129px;background:var(--forest);border-radius:50% 0 50% 50%;display:flex;align-items:center;justify-content:center}
.cat p{margin-top:34px;font-size:20px;font-weight:500}

/* products */
.products{left:0;top:1798px;width:1200px;height:669px;background:var(--forest)}
.products-title{left:0;top:1832px;width:1200px;text-align:center;font-size:56px;color:#fff}
.card{top:1950px;width:317px;height:355px;background:#fff}
.card .shot{position:absolute;left:8px;top:8px;right:8px;height:229px}
.card .tab{position:absolute;right:16px;top:0;width:46px;height:98px;background:var(--ink);display:flex;flex-direction:column;align-items:center;justify-content:space-around;padding:8px 0}
.card h3{position:absolute;left:16px;top:266px;width:180px;font-size:16.5px;font-weight:400;letter-spacing:1px;line-height:34px;text-transform:uppercase}
.card .price{position:absolute;right:16px;top:280px;width:90px;height:36px;border:1px solid #333;border-radius:10px;display:flex;align-items:center;justify-content:center;font-size:16px}
.btn-all{left:483px;top:2354px;width:233px;height:48px;border-radius:30px;background:#fff;color:var(--ink);font-size:18px;letter-spacing:1.5px;font-weight:500;display:flex;align-items:center;justify-content:center}

/* grain */
.grain-bg{left:0;top:2467px;width:1200px;height:707px;background:linear-gradient(#fff 0%,#eef0ee 30%,#b8c1b8 62%,#4a5c4a 88%,var(--forest) 100%)}
.grain-title{left:100px;top:2545px;width:411px;text-align:right;font-size:52px}
.grain-kicker{left:100px;top:2634px;width:410px;text-align:right;font-size:18px;letter-spacing:1px}
.grain-copy{left:60px;top:2682px;width:450px;text-align:right;font-size:15.5px;line-height:37px;white-space:nowrap}
.btn-read2{left:361px;top:2971px;width:148px;height:46px;font-size:18px}
.tile{background:#fff;box-shadow:0 3px 14px rgba(0,0,0,.18);padding:9px}
.tile div{width:100%;height:100%}

/* press */
.press-title{left:0;top:3250px;width:1200px;text-align:center;font-size:58px}
.press{left:112px;top:3374px;width:976px;height:108px;display:flex;align-items:center}
.press span{flex:1;text-align:center;font-size:22px;font-weight:500;color:var(--forest)}
.press b{width:1px;height:108px;background:#999}

/* footer */
.footer{left:0;top:3586px;width:1200px;height:373px;background:var(--forest);color:#fff}
.f-brand{left:85px;top:3712px;font-size:22px;font-weight:500;display:flex;align-items:center;gap:10px;color:#fff}
.f-brand i{width:30px;height:30px;border-radius:50%;background:#fff;opacity:.85}
.social{top:3780px;width:26px;height:26px;border-radius:50%;background:#fff}
.f-head{font-size:19px;font-weight:500;letter-spacing:1px;line-height:40px;color:#fff}
.f-links{font-size:15px;line-height:36px;color:#fff;list-style:none}
.f-label{left:878px;top:3740px;font-size:14px;color:#fff}
.f-line{left:878px;top:3772px;width:238px;height:1px;background:#aaa}
.btn-submit{left:879px;top:3800px;width:107px;height:30px;border-radius:20px;background:#fff;color:var(--ink);font-size:12.5px;font-weight:500;display:flex;align-items:center;justify-content:center}
.copyright{left:0;top:3915px;width:1200px;text-align:center;font-size:14px;color:#fff}
</style>
</head>
<body>

<!-- header -->
<div class="abs topbar">
  <span class="phone"><svg width="16" height="16" viewBox="0 0 24 24"><path fill="#fff" d="M6.6 10.8a15 15 0 0 0 6.6 6.6l2.2-2.2c.3-.3.7-.4 1-.2 1.1.4 2.3.6 3.6.6.6 0 1 .4 1 1V20c0 .6-.4 1-1 1A17 17 0 0 1 3 4c0-.6.4-1 1-1h3.5c.6 0 1 .4 1 1 0 1.3.2 2.5.6 3.6.1.3 0 .7-.2 1z"/></svg>+1 555-014-2290</span>
  <span class="mail"><svg width="16" height="12" viewBox="0 0 24 18"><rect x="1" y="1" width="22" height="16" fill="none" stroke="#fff" stroke-width="2"/><path d="M1 1l11 9 11-9" fill="none" stroke="#fff" stroke-width="2"/></svg>INFO@ALDERSTUDIO.COM</span>
</div>
<svg class="abs cart" width="30" height="28" viewBox="0 0 30 28"><path d="M1 3h5l4 15h15l3-11H8" fill="none" stroke="#222" stroke-width="2"/><circle cx="12" cy="24" r="2" fill="#222"/><circle cx="23" cy="24" r="2" fill="#222"/></svg>
<div class="abs brand"><span>mossrivertwine</span><i></i><small>by alder studio</small></div>
<a class="abs nav active" style="left:467px">HOME</a>
<a class="abs nav" style="left:550px">ABOUT US</a>
<a class="abs nav" style="left:662px">SHOP</a>
<a class="abs nav" style="left:742px">CUSTOM ORDER</a>
<a class="abs nav" style="left:900px">FEEDBACK</a>
<a class="abs nav" style="left:1019px">CONTACT</a>

<!-- hero -->
<div class="abs hero-forest" role="img" aria-label="Misty evergreen forest with a torn paper edge"></div>
<h1 class="abs script hero-title">Made By Hand</h1>
<div class="abs hero-tag">FROM NATURE, REFINED</div>
<p class="abs hero-copy">Inspired by the beauty and usefulness of wood, I started playing<br>with sticks. This is my process of realizing their potential.</p>
<a class="abs btn btn-shop">SHOP NOW</a>
<div class="abs hero-card"><div role="img" aria-label="Hand-carved hooks on a wood slice with dried flowers and grasses"></div></div>

<!-- intro -->
<h2 class="abs script craft-title">More Than Just Tools. It's Art For Your Craft.</h2>
<div class="abs photo-a" role="img" aria-label="Sunflowers, a notebook and a carved hook on a wooden table"></div>
<div class="abs photo-b"><div role="img" aria-label="Jar of carved crochet hooks before a painted canvas"></div></div>
<p class="abs intro-lead">Inspired by the beauty and usefulness of<br>wood, I started playing with sticks. This is<br>my process of realizing their potential.</p>
<p class="abs intro-copy">I create heirloom crochet hooks and knitting needles:<br>rustic, refined or embellished with hand-painted art.<br>Each one is unique, and all are hand-carved from the<br>trees that grace our landscape.</p>
<a class="abs btn btn-read">READ MORE</a>
<div class="abs doily" role="img" aria-label="Crocheted lace doily"></div>

<div class="abs cats">
  <div class="cat"><div class="cat-icon"><svg width="60" height="80" viewBox="0 0 60 80"><circle cx="40" cy="10" r="6" fill="none" stroke="#fff" stroke-width="3"/><path d="M40 16v40a14 14 0 0 1-28 0v-8" fill="none" stroke="#fff" stroke-width="3"/></svg></div><p>RUSTIC HOOKS</p></div>
  <div class="cat"><div class="cat-icon"><svg width="70" height="60" viewBox="0 0 70 60"><rect x="6" y="24" width="58" height="30" fill="none" stroke="#fff" stroke-width="3"/><path d="M6 24l10-14M64 24l-10-14M6 34h58M6 44h58M20 24v30M35 24v30M50 24v30" stroke="#fff" stroke-width="2" fill="none"/></svg></div><p>ART HOOKS</p></div>
  <div class="cat"><div class="cat-icon"><svg width="50" height="80" viewBox="0 0 50 80"><g fill="none" stroke="#fff" stroke-width="3"><circle cx="14" cy="10" r="5"/><circle cx="14" cy="30" r="6"/><path d="M14 36v30"/><circle cx="36" cy="10" r="5"/><circle cx="36" cy="30" r="6"/><path d="M36 36v30"/></g></svg></div><p>HOOK JEWELRY</p></div>
</div>

<!-- products -->
<section class="abs products"></section>
<h2 class="abs script products-title">Our Products</h2>
<article class="abs card" style="left:112px"><div class="shot" role="img" aria-label="Glittery peacock feather hooks beside a fern frond" style="background:linear-gradient(135deg,#e9ece6,#fff 50%,#d8c79a)"></div><div class="tab"><svg width="20" height="18" viewBox="0 0 24 22"><path d="M12 20S2 13 2 7a5 5 0 0 1 10-1 5 5 0 0 1 10 1c0 6-10 13-10 13z" fill="none" stroke="#fff" stroke-width="2"/></svg><svg width="22" height="20" viewBox="0 0 30 28"><path d="M1 3h5l4 15h15l3-11H8" fill="none" stroke="#fff" stroke-width="2"/><circle cx="12" cy="24" r="2" fill="#fff"/><circle cx="23" cy="24" r="2" fill="#fff"/></svg></div><h3>Glittery Peacock Feather</h3><span class="price">$55.00</span></article>
<article class="abs card" style="left:443px"><div class="shot" role="img" aria-label="Lavender hook beside a pot of lavender" style="background:linear-gradient(90deg,#f3efe6,#fff 50%,#9b86c0)"></div><div class="tab"><svg width="20" height="18" viewBox="0 0 24 22"><path d="M12 20S2 13 2 7a5 5 0 0 1 10-1 5 5 0 0 1 10 1c0 6-10 13-10 13z" fill="none" stroke="#fff" stroke-width="2"/></svg><svg width="22" height="20" viewBox="0 0 30 28"><path d="M1 3h5l4 15h15l3-11H8" fill="none" stroke="#fff" stroke-width="2"/><circle cx="12" cy="24" r="2" fill="#fff"/><circle cx="23" cy="24" r="2" fill="#fff"/></svg></div><h3>Lavender Hook, Made To Order</h3><span class="price">$150.00</span></article>
<article class="abs card" style="left:773px"><div class="shot" role="img" aria-label="Hand holding a carved hook before a snowy mountain lake" style="background:linear-gradient(#fff,#c9d6e4 45%,#3f5878 75%,#e8eef3)"></div><div class="tab"><svg width="20" height="18" viewBox="0 0 24 22"><path d="M12 20S2 13 2 7a5 5 0 0 1 10-1 5 5 0 0 1 10 1c0 6-10 13-10 13z" fill="none" stroke="#fff" stroke-width="2"/></svg><svg width="22" height="20" viewBox="0 0 30 28"><path d="M1 3h5l4 15h15l3-11H8" fill="none" stroke="#fff" stroke-width="2"/><circle cx="12" cy="24" r="2" fill="#fff"/><circle cx="23" cy="24" r="2" fill="#fff"/></svg></div><h3>Detailed Roses &amp; Black Smoke</h3><span class="price">$165.00</span></article>
<a class="abs btn-all">VIEW ALL PRODUCTS</a>

<!-- grainlines -->
<div class="abs grain-bg" role="img" aria-label="Foggy forest treeline fading into green"></div>
<h2 class="abs script grain-title">The grainlines go deep...</h2>
<p class="abs grain-kicker">INSPIRED BY WOOD</p>
<p class="abs grain-copy">Wood is inspiring. Even fallen branches and sticks<br>continue the life of the tree in their fibers and seem<br>the perfect accompaniment to wool and other fiber<br>work. My hooks are handmade using a variety of<br>wood sources from our natural landscape. Some<br>hooks are perfect in their rustic state, while others<br>are a backdrop for hand-painted works of art.</p>
<a class="abs btn btn-read2">READ MORE</a>
<div class="abs tile" style="left:593px;top:2564px;width:243px;height:218px"><div role="img" aria-label="Close-up of polished wood grain" style="background:linear-gradient(135deg,#c98f5c,#6b3b22 50%,#d9a878)"></div></div>
<div class="abs tile" style="left:593px;top:2800px;width:243px;height:215px"><div role="img" aria-label="Carved hook beside a dried eucalyptus leaf" style="background:linear-gradient(90deg,#fff,#d3b88c 40%,#bfc2a4 70%,#fff)"></div></div>
<div class="abs tile" style="left:847px;top:2690px;width:241px;height:325px"><div role="img" aria-label="Skeins of hand-dyed yarn with carved hooks" style="background:linear-gradient(#b8653f,#4e7a7a 45%,#c49b5a 70%,#1d1d1d)"></div></div>

<!-- press -->
<h2 class="abs script press-title">As Seen In</h2>
<div class="abs press"><span>Loop Weekly</span><b></b><span>Purl Journal</span><b></b><span>Wren Hollis</span><b></b><span>The Yarn Loft</span><b></b><span>Tessa Lorne</span></div>

<!-- footer -->
<footer class="abs footer"></footer>
<div class="abs f-brand"><span>mossrivertwine</span><i></i></div>
<span class="abs social" style="left:156px"></span>
<span class="abs social" style="left:193px"></span>
<span class="abs social" style="left:231px"></span>
<h4 class="abs f-head" style="left:432px;top:3643px">QUICK LINKS</h4>
<ul class="abs f-links" style="left:432px;top:3695px"><li>ABOUT ALDER</li><li>FEEDBACK &amp; REVIEWS</li><li>LOOK-BOOK GALLERY</li><li>GET IN TOUCH</li></ul>
<ul class="abs f-links" style="left:649px;top:3695px"><li>WOOD TYPES</li><li>ART HOOKS</li><li>RUSTIC HOOKS</li><li>CUSTOM HOOKS</li></ul>
<h4 class="abs f-head" style="left:878px;top:3643px;width:200px">MOSS RIVER TWINE</h4>
<span class="abs f-label">EMAIL ADDRESS</span>
<span class="abs f-line"></span>
<a class="abs btn-submit">SUBMIT NOW</a>
<p class="abs copyright">COPYRIGHT © 2024 MOSS RIVER TWINE – ALL RIGHTS RESERVED.</p>

</body>
</html>
```